Business card design for Automotive workshop

We need a business card for a new automotive repair and tyre shop called Keelstone Prime Automotive located in New Zealand. We are a clean, modern and fresh workshop and company.

Front needs to feature logo,
my name:
Marlo Fenwicke (director)

Address:
48 Tarn Lane
Marrowby 3625

Phone: 07 594 2713
Mobile: 027 451 9362
Email: office@keelstoneautomotive.example.nz
Website: keelstoneautomotive.example.nz

Back needs to feature an area to write down appointment details, date and time.

Also feature a list of jobs and work we do such as,
Vehicle Servicing
All Mechanical Repairs
Warrant of Fitness
Tyres & Wheel Alignments
Automotive Diagnostics
Automotive Parts & Supplies

```html
<!DOCTYPE html>
<html lang="en">
<head>
<meta charset="utf-8">
<title>Keelstone Prime Automotive – Business Card</title>
<link rel="stylesheet" href="https://fonts.googleapis.com/css2?family=Montserrat:wght@500;600;700;800&family=Arimo:wght@400&display=swap">
<style>
  :root{
    --red:#e31b23;
    --black:#0b0b0b;
    --white:#ffffff;
    --ink:#111111;
    --grey:#bdbdbd;
    --rule:#c9c9c9;
    --bg:#e9e9e9;
  }
  *{box-sizing:border-box;margin:0;padding:0}
  html,body{width:1200px;height:1200px;overflow:hidden;background:var(--bg)}
  .canvas{position:relative;width:1200px;height:1200px}
  .card{
    position:absolute;left:150px;width:900px;height:500px;
    border-radius:90px 0 90px 0;overflow:hidden;
    box-shadow:0 8px 24px rgba(0,0,0,.18);
  }

  /* Appointment side */
  .card--appointment{top:70px;background:var(--white);display:flex}
  .brand-band{
    width:240px;height:100%;background:var(--red);
    display:flex;align-items:center;justify-content:center;flex:none;
  }
  .brand-band .brand-name{
    transform:rotate(-90deg);white-space:nowrap;
    font-family:'Montserrat',sans-serif;font-weight:700;
    font-size:30px;letter-spacing:1px;color:var(--white);text-transform:uppercase;
    text-align:center;line-height:1.2;
  }
  .appointment{flex:1;padding:48px 60px 0 70px;font-family:'Montserrat',sans-serif;color:var(--ink)}
  .appointment__title{font-weight:800;font-size:26px;letter-spacing:.5px}
  .appointment__fields{display:flex;align-items:flex-end;gap:14px;margin-top:26px;font-family:'Arimo',sans-serif;font-size:25px;letter-spacing:1px}
  .appointment__fields .blank{flex:1;border-bottom:1px solid var(--rule);margin-bottom:6px}
  .services__heading{display:flex;align-items:center;gap:10px;margin-top:38px}
  .services__heading .bar{flex:1;height:6px;background:var(--ink)}
  .services__heading h2{color:var(--red);font-weight:800;font-size:22px;letter-spacing:1px}
  .services__list{list-style:none;margin-top:14px}
  .services__list li{display:flex;align-items:center;gap:14px;font-weight:500;font-size:20px;letter-spacing:1px;line-height:1.45;text-transform:uppercase}
  .services__list li::before{content:"";width:10px;height:10px;background:var(--red);flex:none}

  /* Contact side */
  .card--contact{top:630px;background:var(--black);color:var(--white)}
  .contact__brand{
    position:absolute;right:70px;top:70px;
    font-family:'Montserrat',sans-serif;font-weight:700;font-size:34px;
    color:var(--red);text-transform:uppercase;letter-spacing:1px;text-align:right;line-height:1.15;
  }
  .contact__person{position:absolute;left:70px;top:175px;right:70px}
  .contact__name{font-family:'Montserrat',sans-serif;font-weight:700;font-size:34px;color:var(--red);text-transform:uppercase;letter-spacing:.5px}
  .contact__role{font-family:'Arimo',sans-serif;font-size:22px;color:var(--grey);display:flex;align-items:center;gap:12px;margin-top:2px}
  .contact__role .rule{flex:1;height:1px;background:#3a3a3a;margin-top:10px}
  .contact__list{position:absolute;left:70px;top:300px;list-style:none;font-family:'Arimo',sans-serif;font-size:25px;color:#e6e6e6;line-height:1.32}
  .contact__list li{display:flex;align-items:center;gap:10px}
  .contact__list svg{width:18px;height:18px;flex:none}
  .contact__address{position:absolute;right:70px;bottom:50px;text-align:right;font-family:'Arimo',sans-serif;font-style:normal;font-size:26px;color:#d6d6d6;line-height:1.3}
</style>
</head>
<body>
<main class="canvas">

  <section class="card card--appointment" aria-label="Appointment side">
    <div class="brand-band">
      <p class="brand-name">Keelstone Prime<br>Automotive</p>
    </div>
    <div class="appointment">
      <h1 class="appointment__title">NEXT APPOINTMENT</h1>
      <div class="appointment__fields">
        <span>DATE</span><span class="blank"></span>
        <span>TIME</span><span class="blank"></span>
      </div>
      <div class="services__heading">
        <span class="bar"></span><h2>WORK WE DO</h2><span class="bar"></span>
      </div>
      <ul class="services__list">
        <li>Vehicle Servicing</li>
        <li>All Mechanical Repairs</li>
        <li>Warrant of Fitness</li>
        <li>Tyres &amp; Wheel Alignments</li>
        <li>Automotive Diagnostics</li>
        <li>Automotive Parts &amp; Supplies</li>
      </ul>
    </div>
  </section>

  <section class="card card--contact" aria-label="Contact side">
    <p class="contact__brand">Keelstone Prime<br>Automotive</p>
    <div class="contact__person">
      <h2 class="contact__name">Marlo Fenwicke</h2>
      <p class="contact__role">Director <span class="rule"></span></p>
    </div>
    <ul class="contact__list">
      <li>
        <svg viewBox="0 0 20 20" aria-hidden="true"><path fill="var(--red)" d="M2 6c0-2 2-3 4-3h8c2 0 4 1 4 3v1h-4V5H6v2H2zM5 9h10l3 8H2z"/></svg>
        07 594 2713
      </li>
      <li>
        <svg viewBox="0 0 20 20" aria-hidden="true"><rect x="5" y="1" width="10" height="18" rx="2" fill="none" stroke="var(--red)" stroke-width="2"/></svg>
        027 451 9362
      </li>
      <li>
        <svg viewBox="0 0 20 20" aria-hidden="true"><rect x="1" y="4" width="18" height="12" fill="var(--red)"/><path d="M1 4l9 7 9-7" fill="none" stroke="var(--black)" stroke-width="1.5"/></svg>
        office@keelstoneautomotive.example.nz
      </li>
      <li>
        <svg viewBox="0 0 20 20" aria-hidden="true"><circle cx="10" cy="10" r="8" fill="var(--red)"/><path d="M2 10h16M10 2c-4 4-4 12 0 16M10 2c4 4 4 12 0 16" fill="none" stroke="var(--black)" stroke-width="1.2"/></svg>
        keelstoneautomotive.example.nz
      </li>
    </ul>
    <address class="contact__address">
      48 Tarn Lane<br>Marrowby 3625
    </address>
  </section>

</main>
</body>
</html>
```